NEW Wordpress Website Design for a Dynamic Long Term Healthcare Company in Hawaii

I would like a new website design for my current company, Marlow Health Collective, which has two different brands - Marlow Homecare and Marlow Senior Living. You can see the current website at www.marlowhealth-example.com. The website should be built using Wordpress Software and the Framewise theme. The website should have a local Hawaii island/tropical feel, but look professional for healthcare. I'm looking for something fresh, and want the designer to select colors, styles, etc.

In the Header, on all pages, I would like a menu that includes Home Care, Senior Living, Rates, and About Us.
Under each of the Header Menu Titles, I would like these drop downs included:
Home Care (drop down pages)- Nurse Aide Care, 24-Hour Home Care, Skilled Nursing, Lifestyle Aide, Hospice at Home, Bathing & Meal Service.
Senior Living (drop down pages) - Long-Term Stay, Short-Term Stay.
Rates (drop down page) - Rates.
About Us (drop down pages) - Our Mission, Ohana Talk, About Dana Marlow.

In the footer, on all pages, you should include the address: 248 Pueo Lane, Suite 310, Honolulu, HI 96817. Phone number: 808-555-0172
The footer should also include buttons for a page called Learn, Caregiver Jobs, and each of the service page links to include: Nurse Aide Care, 24-Hour Home Care, Skilled Nursing, Lifestyle Aide, Hospice at Home, Bathing & Meal Service.
Please don't take the current website and redesign a few aspects. I'm looking for a completely different look and feel.

Target Market(s)

40-80 year olds

Industry/Entity Type

Long Term Healthcare

Coding

Coded - Design and coding required

Requirements
Should not have
• Our existing website as a template. We are looking for a complete redesign. Thank you.

```html
<!DOCTYPE html>
<html lang="en">
<head>
<meta charset="utf-8">
<title>Marlow Health Collective — Homecare &amp; Senior Living</title>
<link rel="stylesheet" href="https://fonts.googleapis.com/css2?family=Josefin+Sans:wght@400;600&family=Lora:wght@400&family=Montserrat:wght@400;500;600;700&display=swap">
<style>
:root{
  --orange:#f08a1e;
  --orange-deep:#e0701a;
  --teal:#1aa69a;
  --teal-deep:#12887e;
  --red:#c8372a;
  --ink:#222;
  --body:#555;
  --cream:#faf6ec;
  --white:#fff;
}
*{box-sizing:border-box;margin:0;padding:0}
html,body{width:1200px;height:4605px;overflow:hidden}
body{font-family:"Montserrat",sans-serif;color:var(--ink);background:var(--white);position:relative}
.abs{position:absolute}
a{color:inherit;text-decoration:none}
.placeholder{position:absolute}
.h2{font-family:"Josefin Sans",sans-serif;font-weight:400;font-size:46px;line-height:54px;color:var(--ink);letter-spacing:.5px}
.swash{display:block;width:60px;height:10px;margin-top:6px}
.para{font-size:15px;line-height:28px;color:var(--body)}
.btn{position:absolute;display:flex;align-items:center;justify-content:center;gap:6px;border-radius:30px;font-size:14px;font-weight:600;letter-spacing:.5px;text-transform:uppercase}
.btn-orange{background:linear-gradient(90deg,var(--orange-deep),var(--orange));color:var(--white)}
.btn-teal{background:var(--teal);color:var(--white)}
.btn-outline{border:2px solid var(--teal);color:var(--teal);background:var(--white)}
.chev{width:8px;height:10px}
.svc-list{position:absolute;display:grid;grid-template-columns:225px 225px;row-gap:16px;font-size:15px;font-weight:600;color:#333}
.svc-list li{list-style:none;display:flex;align-items:center;gap:12px}

/* header */
.site-header{top:0;left:0;width:1200px;height:107px}
.brand{position:absolute;display:flex;align-items:center;gap:10px}
.brand-dot{width:40px;height:40px;border-radius:50%;background:var(--orange-deep);flex:none}
.brand-name{font-family:"Josefin Sans",sans-serif;font-weight:600;color:var(--red);font-size:20px;line-height:22px}
.main-nav{position:absolute;top:34px;left:390px;display:flex;gap:0;font-size:13px;font-weight:500;color:#333}
.main-nav span{display:flex;align-items:center;gap:5px}
.phone-btn{top:27px;left:923px;width:186px;height:38px;font-size:14px}

/* hero */
.hero-title{top:128px;left:0;width:1200px;text-align:center}
.hero-kicker{font-family:"Josefin Sans",sans-serif;font-size:28px;color:var(--red);letter-spacing:1px;text-transform:uppercase}
.hero-heading{font-family:"Lora",serif;font-weight:400;font-size:54px;color:#222;margin-top:4px}

/* testimonials */
.t-card{position:absolute;background:var(--white);box-shadow:0 6px 20px rgba(0,0,0,.12);text-align:center}
.t-arrow{position:absolute;width:36px;height:36px;border-radius:50%;background:var(--teal)}

/* form */
.field{position:absolute;background:var(--white);font-size:13px;color:#555;padding:13px 18px}

/* footer */
.f-col h3{font-family:"Josefin Sans",sans-serif;font-weight:400;font-size:21px;color:#222;margin-bottom:14px}
.f-col li{list-style:none;font-size:13px;color:#444;display:flex;gap:8px;align-items:center;margin-bottom:13px}
.f-col li::before{content:"›";color:var(--orange)}
.f-divider{position:absolute;top:4200px;width:2px;height:330px;background:#f0d9bf}
</style>
</head>
<body>

<!-- Hero -->
<div class="placeholder" role="img" aria-label="Three smiling older women knitting together on a sofa in a sunny tropical living room" style="top:0;left:0;width:1200px;height:710px;background:linear-gradient(180deg,#fbf6d8 0%,#f2ebbd 40%,#d8b98a 75%,#b98d5e 100%)"></div>
<div class="abs" style="top:0;left:0;width:1200px;height:360px;background:linear-gradient(180deg,rgba(255,255,255,.85),rgba(255,255,255,0))"></div>

<header class="abs site-header">
  <div class="brand" style="top:24px;left:98px;width:260px">
    <span class="brand-dot"></span>
    <span class="brand-name">Marlow Health<br>Collective</span>
  </div>
  <nav class="main-nav">
    <span style="width:141px">HOME CARE <svg class="chev" viewBox="0 0 10 6"><path d="M1 1l4 4 4-4" fill="none" stroke="#888" stroke-width="1.3"/></svg></span>
    <span style="width:161px">SENIOR LIVING <svg class="chev" viewBox="0 0 10 6"><path d="M1 1l4 4 4-4" fill="none" stroke="#888" stroke-width="1.3"/></svg></span>
    <span style="width:97px">RATES <svg class="chev" viewBox="0 0 10 6"><path d="M1 1l4 4 4-4" fill="none" stroke="#888" stroke-width="1.3"/></svg></span>
    <span>ABOUT US <svg class="chev" viewBox="0 0 10 6"><path d="M1 1l4 4 4-4" fill="none" stroke="#888" stroke-width="1.3"/></svg></span>
  </nav>
  <a class="btn btn-orange phone-btn">
    <svg width="18" height="18" viewBox="0 0 20 20"><circle cx="10" cy="10" r="10" fill="#fff"/><path d="M7 5l2 2-1 2c1 2 2 3 4 4l2-1 2 2-2 2c-4 0-9-5-9-9z" fill="var(--orange)"/></svg>
    (808) 555-0172
  </a>
</header>

<div class="abs hero-title">
  <div class="hero-kicker">— Marlow Health Collective —</div>
  <h1 class="hero-heading">Homecare &amp; Senior Living</h1>
</div>
<a class="btn btn-orange" style="top:250px;left:506px;width:188px;height:48px">View Rates <svg class="chev" viewBox="0 0 8 10"><path d="M2 1l4 4-4 4" fill="none" stroke="#fff" stroke-width="1.6"/></svg></a>

<!-- Our Mission -->
<section class="abs" style="top:710px;left:0;width:1200px;height:568px">
  <div class="placeholder" role="img" aria-label="Caregiver helping a woman with a walker in a tropical garden, framed in a heart shape" style="top:64px;left:120px;width:416px;height:442px;border-radius:40px;background:linear-gradient(160deg,#fbe6b8,#7fa05c 40%,#4d7a3e 70%,#eef0e8)"></div>
  <div class="abs" style="top:100px;left:603px">
    <h2 class="h2">Our Mission</h2>
    <svg class="swash" viewBox="0 0 60 10"><path d="M2 7q28-8 56 0" fill="none" stroke="var(--orange)" stroke-width="3"/><path d="M8 9h44" stroke="var(--orange)" stroke-width="1"/></svg>
  </div>
  <p class="abs para" style="top:193px;left:603px;width:490px">At Marlow Health Collective, our mission is to provide compassionate and professional long-term healthcare services that empower individuals to maintain their highest level of independence, health, and well-being in the comfort of their own homes or ours, either through our licensed home healthcare agency</p>
  <a class="btn btn-outline" style="top:398px;left:603px;width:198px;height:51px">Learn More <svg class="chev" viewBox="0 0 8 10"><path d="M2 1l4 4-4 4" fill="none" stroke="var(--teal)" stroke-width="1.6"/></svg></a>
</section>

<!-- Home Care -->
<section class="abs" style="top:1278px;left:0;width:1200px;height:578px;background:linear-gradient(120deg,#f7f4ea,#fbfaf5 50%,#f2efe4)">
  <div class="abs" style="top:124px;left:122px">
    <h2 class="h2">Home Care</h2>
    <svg class="swash" viewBox="0 0 60 10"><path d="M2 7q28-8 56 0" fill="none" stroke="var(--orange)" stroke-width="3"/></svg>
  </div>
  <p class="abs para" style="top:200px;left:122px;width:420px;font-size:14px;line-height:24px">Marlow Homecare understands that every person's care journey is unique. We tailor our in-home services to meet the diverse nurturing experience</p>
  <ul class="svc-list" style="top:298px;left:126px">
    <li><svg class="chev" viewBox="0 0 8 10"><path d="M2 1l4 4-4 4" fill="none" stroke="var(--orange)" stroke-width="2"/></svg>Nurse Aide Care</li>
    <li><svg class="chev" viewBox="0 0 8 10"><path d="M2 1l4 4-4 4" fill="none" stroke="var(--orange)" stroke-width="2"/></svg>Lifestyle Aide</li>
    <li><svg class="chev" viewBox="0 0 8 10"><path d="M2 1l4 4-4 4" fill="none" stroke="var(--orange)" stroke-width="2"/></svg>24-Hour Home Care</li>
    <li><svg class="chev" viewBox="0 0 8 10"><path d="M2 1l4 4-4 4" fill="none" stroke="var(--orange)" stroke-width="2"/></svg>Hospice at Home</li>
    <li><svg class="chev" viewBox="0 0 8 10"><path d="M2 1l4 4-4 4" fill="none" stroke="var(--orange)" stroke-width="2"/></svg>Skilled Nursing</li>
    <li><svg class="chev" viewBox="0 0 8 10"><path d="M2 1l4 4-4 4" fill="none" stroke="var(--orange)" stroke-width="2"/></svg>Bathing &amp; Meal Service</li>
  </ul>
  <a class="btn btn-orange" style="top:438px;left:118px;width:186px;height:49px">Learn More <svg class="chev" viewBox="0 0 8 10"><path d="M2 1l4 4-4 4" fill="none" stroke="#fff" stroke-width="1.6"/></svg></a>
  <div class="abs" style="top:108px;left:620px;width:489px;height:359px;border:2px solid var(--teal);border-radius:0 0 60px 0"></div>
  <div class="placeholder" role="img" aria-label="Nurse in scrubs visiting an older woman on a sofa in a bright island home" style="top:102px;left:612px;width:489px;height:359px;border-radius:60px 0 60px 0;background:linear-gradient(135deg,#e7dfb8,#c8b27a 45%,#6f8f9c 75%,#8a6b4a)"></div>
</section>

<!-- Senior Living -->
<section class="abs" style="top:1856px;left:0;width:1200px;height:570px;background:var(--white)">
  <svg class="abs" style="top:0;left:0" width="400" height="570" viewBox="0 0 400 570" role="img" aria-label="Teal panel with faint palm leaves">
    <path d="M0 0H385Q330 40 300 150 260 360 270 470 275 540 290 570H0Z" fill="var(--teal)"/>
  </svg>
  <div class="placeholder" role="img" aria-label="Caregiver helping an older man rise from his bed in a care home room" style="top:79px;left:77px;width:495px;height:366px;border-radius:60px 0 60px 0;background:linear-gradient(135deg,#e6e0a2,#c9b37b 40%,#8a8c6f 70%,#3f8fb2)"></div>
  <div class="abs" style="top:89px;left:580px;width:2px;height:362px;background:var(--teal)"></div>
  <div class="abs" style="top:100px;left:631px">
    <h2 class="h2">Senior Living</h2>
    <svg class="swash" viewBox="0 0 60 10"><path d="M2 7q28-8 56 0" fill="none" stroke="var(--teal)" stroke-width="3"/></svg>
  </div>
  <p class="abs para" style="top:190px;left:631px;width:450px;font-size:15px;line-height:27px">Marlow Senior Living creates a warm, supportive, and enriching care home environment where seniors can thrive in their golden years. We provide residential care that promotes well-being, connection, and dignity of each individual.</p>
  <ul class="svc-list" style="top:350px;left:633px;grid-template-columns:211px 200px;font-size:14px">
    <li><svg class="chev" viewBox="0 0 8 10"><path d="M2 1l4 4-4 4" fill="none" stroke="var(--teal)" stroke-width="2"/></svg>LONG-TERM STAY</li>
    <li><svg class="chev" viewBox="0 0 8 10"><path d="M2 1l4 4-4 4" fill="none" stroke="var(--teal)" stroke-width="2"/></svg>SHORT-TERM STAY</li>
  </ul>
  <a class="btn btn-teal" style="top:406px;left:629px;width:186px;height:50px">Learn More <svg class="chev" viewBox="0 0 8 10"><path d="M2 1l4 4-4 4" fill="none" stroke="#fff" stroke-width="1.6"/></svg></a>
</section>

<!-- Testimonials -->
<section class="abs" style="top:2426px;left:0;width:1200px;height:599px;background:linear-gradient(180deg,#f59a2a,#ef8a1c)">
  <h2 class="abs" style="top:72px;left:0;width:1200px;text-align:center;font-family:'Josefin Sans',sans-serif;font-weight:400;font-size:50px;color:var(--white)">Testimonials</h2>
  <svg class="abs" style="top:130px;left:568px" width="64" height="12" viewBox="0 0 60 10"><path d="M2 7q28-8 56 0" fill="none" stroke="#fff" stroke-width="3"/></svg>

  <div class="t-card" style="top:217px;left:163px;width:240px;height:236px;padding:30px 60px 0 20px;font-size:12px;line-height:19px;color:#444">Lorem ipsum dolor sit amet, sed do eiusmod tempor magna aliqua. Ut enim exercitation ullamco commodo consequat reprehenderit in voluptate</div>
  <div class="t-card" style="top:222px;left:800px;width:273px;height:236px;padding:30px 24px 0 90px;font-size:12px;line-height:19px;color:#444;text-align:left">consectetur adipiscing elit, sed ut labore et dolore veniam, quis nostrud nisi ut aliquip ex ea aute irure dolor in esse cillum dolore eu
    <span class="abs" style="bottom:26px;right:18px;width:22px;height:22px;border-radius:50%;background:#cfcfcf"></span>
  </div>

  <div class="t-card" style="top:183px;left:345px;width:542px;height:320px;padding:48px 60px 0">
    <svg class="abs" style="top:46px;left:46px" width="26" height="20" viewBox="0 0 26 20"><path d="M2 20V11Q2 2 11 0v4Q6 6 6 10h5v10ZM15 20V11Q15 2 24 0v4q-5 2-5 6h5v10Z" fill="var(--orange)"/></svg>
    <p style="font-size:16px;line-height:24px;color:#333">Lorem ipsum dolor sit amet, consectetur adipiscing elit, sed do eiusmod tempor incididunt ut labore et dolore magna aliqua. Ut enim ad minim veniam, quis nostrud exercitation ullamco laboris nisi ut aliquip ex ea commodo consequat. Duis aute irure dolor in reprehenderit in voluptate velit esse cillum dolore eu fugiat nulla</p>
    <svg class="abs" style="top:212px;left:482px" width="26" height="20" viewBox="0 0 26 20"><path d="M24 0v9q0 9-9 11v-4q5-2 5-6h-5V0ZM11 0v9q0 9-9 11v-4q5-2 5-6H2V0Z" fill="var(--orange)"/></svg>
    <p style="margin-top:22px;font-size:15px;font-weight:700;text-decoration:underline;color:#222">Trustline Review</p>
    <span class="abs" style="bottom:22px;right:22px;width:26px;height:26px;border-radius:50%;background:#cfcfcf"></span>
  </div>

  <span class="t-arrow" style="top:319px;left:100px"><svg width="36" height="36" viewBox="0 0 36 36"><path d="M24 18H12m5-5l-5 5 5 5" fill="none" stroke="#fff" stroke-width="2"/></svg></span>
  <span class="t-arrow" style="top:323px;left:1103px"><svg width="36" height="36" viewBox="0 0 36 36"><path d="M12 18h12m-5-5l5 5-5 5" fill="none" stroke="#fff" stroke-width="2"/></svg></span>
</section>

<!-- Rates -->
<section class="abs" style="top:3025px;left:0;width:1200px;height:605px;background:linear-gradient(180deg,#f1f6f6,#ffffff 70%)">
  <div class="abs" style="top:110px;left:120px">
    <h2 class="h2">Rates &amp; Pricing</h2>
    <svg class="swash" viewBox="0 0 60 10"><path d="M2 7q28-8 56 0" fill="none" stroke="var(--orange)" stroke-width="3"/></svg>
  </div>
  <p class="abs para" style="top:203px;left:122px;width:490px;font-size:15px;line-height:28px">At Marlow Health Collective, our mission is to provide compassionate and professional long-term healthcare services that empower individuals to maintain their highest level of independence, health, and well-being in the comfort of their own homes or ours, either through our licensed home healthcare agency</p>
  <a class="btn btn-outline" style="top:408px;left:120px;width:198px;height:53px">Learn More <svg class="chev" viewBox="0 0 8 10"><path d="M2 1l4 4-4 4" fill="none" stroke="var(--teal)" stroke-width="1.6"/></svg></a>
  <div class="abs" style="top:40px;left:612px;width:448px;height:448px;border-radius:50%;border:5px solid var(--teal);border-right-color:var(--orange);border-bottom-color:var(--orange)"></div>
  <div class="placeholder" role="img" aria-label="Caregiver walking beside a woman using a walker outdoors among palms" style="top:50px;left:622px;width:428px;height:428px;border-radius:50%;background:linear-gradient(150deg,#cfe0b0,#7fa25e 40%,#5d7f68 70%,#d9d2c4)"></div>
  <div class="placeholder" role="img" aria-label="Portrait of a smiling nurse" style="top:303px;left:831px;width:210px;height:210px;border-radius:50%;border:5px solid var(--white);background:linear-gradient(160deg,#f1ece6,#c99779 60%,#8a5a44)"></div>
</section>

<!-- Consultation -->
<section class="abs" style="top:3633px;left:98px;width:998px;height:533px;border-radius:60px 0 60px 0;overflow:hidden;background:var(--teal)">
  <div class="placeholder" role="img" aria-label="Caregiver serving breakfast to an older couple at a dining table" style="top:0;left:510px;width:488px;height:533px;background:linear-gradient(90deg,var(--teal) 0%,#b9c7a8 25%,#e6dcc4 60%,#c7b497)"></div>
  <h2 class="abs" style="top:80px;left:92px;font-family:'Josefin Sans',sans-serif;font-weight:400;font-size:34px;line-height:43px;color:var(--white)">Schedule a Complimentary<br>are Consultation</h2>
  <svg class="abs" style="top:175px;left:94px" width="60" height="10" viewBox="0 0 60 10"><path d="M2 7q28-8 56 0" fill="none" stroke="#fff" stroke-width="3"/></svg>
  <div class="field" style="top:190px;left:92px;width:206px;height:45px">First Name</div>
  <div class="field" style="top:190px;left:310px;width:203px;height:45px">Last Name</div>
  <div class="field" style="top:244px;left:92px;width:206px;height:45px">Email address</div>
  <div class="field" style="top:244px;left:310px;width:203px;height:45px">Phone Number</div>
  <div class="field" style="top:297px;left:92px;width:421px;height:102px">Message</div>
  <a class="btn" style="top:418px;left:92px;width:180px;height:44px;background:var(--teal-deep);color:var(--white)">Send Message <svg class="chev" viewBox="0 0 8 10"><path d="M2 1l4 4-4 4" fill="none" stroke="#fff" stroke-width="1.6"/></svg></a>
</section>

<!-- Footer -->
<footer class="abs" style="top:4166px;left:0;width:1200px;height:439px">
  <div class="abs" style="top:58px;left:155px;width:170px;text-align:center">
    <span class="brand-dot" style="display:block;margin:0 auto 10px;width:56px;height:56px"></span>
    <span class="brand-name" style="display:block;font-size:22px;line-height:26px">Marlow Health Collective</span>
  </div>
  <a class="btn" style="top:211px;left:155px;width:169px;height:30px;border:1px solid var(--orange);color:var(--orange);border-radius:0;font-size:11px">Learn</a>
  <a class="btn btn-orange" style="top:259px;left:155px;width:169px;height:33px;border-radius:0;font-size:11px">Care Giver Jobs</a>
</footer>
<div class="f-divider" style="left:390px"></div>
<div class="f-divider" style="left:599px"></div>
<div class="f-divider" style="left:830px"></div>

<div class="abs f-col" style="top:4232px;left:415px">
  <h3>Navigation</h3>
  <ul><li>Home Care</li><li>Senior Living</li><li>Rates</li><li>About Us</li></ul>
</div>
<div class="abs f-col" style="top:4232px;left:620px">
  <h3>Services</h3>
  <ul><li>Nurse Aide Care</li><li>24-Hour Home Care</li><li>Skilled Nursing</li><li>Lifestyle Aide</li><li>Hospice at Home</li><li>Bathing &amp; Meal Service</li></ul>
</div>
<div class="abs f-col" style="top:4232px;left:850px;width:250px">
  <h3>Contact Us</h3>
  <div style="display:flex;gap:12px;font-size:13px;line-height:18px;color:#333">
    <svg width="30" height="30" viewBox="0 0 30 30" style="flex:none"><circle cx="15" cy="15" r="15" fill="var(--teal)"/><path d="M15 7a5 5 0 0 0-5 5c0 4 5 10 5 10s5-6 5-10a5 5 0 0 0-5-5z" fill="#fff"/><circle cx="15" cy="12" r="2" fill="var(--teal)"/></svg>
    <span>248 Pueo Lane, Suite 310,<br>Honolulu, HI 96817</span>
  </div>
  <div style="display:flex;gap:12px;font-size:13px;line-height:18px;color:#333;margin-top:14px">
    <svg width="30" height="30" viewBox="0 0 30 30" style="flex:none"><circle cx="15" cy="15" r="15" fill="var(--teal)"/><path d="M11 8l3 3-1.5 2c1 2 3 4 5 5l2-1.5 3 3-2 2c-6 0-12-6-12-12z" fill="#fff"/></svg>
    <span>Phone number<br><b style="font-size:14px">808-555-0172</b></span>
  </div>
  <div style="display:flex;gap:8px;margin-top:20px;padding-left:6px">
    <span style="width:30px;height:30px;border-radius:50%;background:var(--red)"></span>
    <span style="width:30px;height:30px;border-radius:50%;background:var(--teal)"></span>
    <span style="width:30px;height:30px;border-radius:50%;background:var(--teal)"></span>
    <span style="width:30px;height:30px;border-radius:50%;background:var(--teal)"></span>
  </div>
</div>

<div class="abs" style="top:4541px;left:0;width:1200px;height:1px;background:#eadfce"></div>
<p class="abs" style="top:4562px;left:0;width:1200px;text-align:center;font-size:11px;color:#444">Copyright © 2024 <u>Marlow Health Collective</u>. All Right Reserved</p>

</body>
</html>
```